Restaurant Menu New Design

Hello Designers,

Blue Fern is a casual family oriented dine-in restaurant, we serve American Italian dishes like Pizza, Pasta, and Sandwiches.

We are excited about adding some new delicious dishes and recipes to our menu. And we are looking for a talented and creative designer to design it.

The menu is a 12 page black leather book, page size is:
6.5" X 11.69" (16.51 cm X 29.69 cm)

Below is the scope of work and requirements:

1) Design a completely all new, creative, and beautiful menu, including cover page, blue fern oven intro. page, interior pages, and kids menu page.

2) Design a take out edition of the menu. It will be exactly the same as the dine-in menu, but with the addition of a back cover page with info such as contacts, social media, location map, etc…

3) Files are required in Adobe Illustrator format. Layers should be organized, all text should be editable, and all the food pictures easy to change.

4) This is a two language menu, so you are required to make space in the design for a second language. The easiest way to do that is have every item listed in English twice, then I will edit the second text with Illustrator.

5) In your initial design submission, the minimum you are required to submit are these 4 pages:
– Cover page
– Typical interior menu page
– Kids menu page
– Take-out menu back cover page

If your initial design is selected, then you are required to submit all remaining pages to complete the project.

In the link below, you will find:
1) Logo
2) New menu text in Excel
3) Food images (will take some time to upload)
4) The old dine-in and take out menu designs

https://www.filevaultra.com/sh/kq7tmwzabe3pxd/BBBrTnpLk41QaWmZpQ8V2X7Jd?dl=0

Thank you for stopping by and reading this brief. I hope you like this project and enjoy designing our new menu. Please let me know if you have any questions.

Cheers!

Project Deadline Extended
Reason: We have decided to extend the deadline due to the low number of submissions which was much lower than the expected submissions we were give by Brief Harbor.

```html
<!DOCTYPE html>
<html lang="en">
<head>
<meta charset="utf-8">
<title>Main Course</title>
<link rel="stylesheet" href="https://fonts.googleapis.com/css2?family=Lato:wght@300;400;700&family=Noto+Sans+Arabic:wght@300;400;600&display=swap">
<style>
:root{
  --board:#333335;
  --line:#e9e9e9;
  --title:#ffffff;
  --body:#a8a8aa;
  --doodle:rgba(255,255,255,0.09);
}
*{margin:0;padding:0;box-sizing:border-box}
html,body{width:1200px;height:2161px;overflow:hidden;background:var(--board)}
.menu-page{position:relative;width:1200px;height:2161px;background:var(--board);font-family:'Lato',sans-serif;color:var(--title)}
.frame-lines{position:absolute;left:0;top:0}
.heading{position:absolute;top:62px;font-size:38px;font-weight:400;letter-spacing:1px;transform:translateX(-50%)}
.photo{position:absolute}
.photo-grilled{left:72px;top:235px;width:461px;height:306px;background:linear-gradient(160deg,#c98a4e,#f1ece4 45%,#b8743c)}
.photo-milanese{left:664px;top:235px;width:462px;height:306px;background:linear-gradient(160deg,#c48b50,#b36a2e 50%,#e9e2d6)}
.photo-shrimp{left:72px;top:929px;width:461px;height:307px;background:linear-gradient(150deg,#e6e3de,#c47a45 50%,#9aa05a)}
.photo-stroganoff{left:664px;top:929px;width:462px;height:307px;background:linear-gradient(150deg,#5c8a3a,#e8cf8a 45%,#b99a70)}
.photo-steak{left:662px;top:1663px;width:464px;height:308px;background:linear-gradient(150deg,#b04a3a,#4a2a1e 50%,#3f7a2a)}
.doodle{position:absolute;background:var(--doodle);border-radius:50%}
.dish{position:absolute;width:520px;text-align:center;transform:translateX(-50%)}
.dish-name{font-size:25px;font-weight:700;line-height:30px;letter-spacing:.2px}
.dish-name-ar{font-family:'Noto Sans Arabic',sans-serif;font-size:24px;font-weight:400;line-height:34px;direction:rtl}
.dish-desc{margin-top:24px;font-size:16.5px;font-weight:400;line-height:22px;color:var(--body);padding:0 30px}
.dish-desc-ar{margin-top:20px;font-family:'Noto Sans Arabic',sans-serif;font-size:15.5px;font-weight:300;line-height:22px;color:var(--body);direction:rtl;padding:0 30px}
</style>
</head>
<body>
<main class="menu-page">

<svg class="frame-lines" width="1200" height="2161" viewBox="0 0 1200 2161" fill="none" stroke="var(--line)" stroke-width="2.5">
  <line x1="0" y1="125" x2="360" y2="125"/>
  <line x1="878" y1="125" x2="1200" y2="125"/>
  <polyline points="446,209 55,209 55,540"/>
  <polyline points="1163,317 1163,569 1109,569"/>
  <path d="M55 560 C20 610 70 650 45 700 C20 760 60 820 55 880"/>
  <polyline points="749,888 1163,888 1163,1130"/>
  <polyline points="40,1015 40,1274 238,1274"/>
  <line x1="0" y1="1598" x2="343" y2="1598"/>
  <line x1="858" y1="1598" x2="1200" y2="1598"/>
  <polyline points="46,1678 46,2023 1037,2023"/>
  <polyline points="1066,1642 1163,1642 1163,1886"/>
  <line x1="0" y1="2069" x2="1200" y2="2069" stroke-width="2"/>
  <g stroke-width="2.5">
    <path d="M545 154 h110"/>
    <path d="M556 146 a44 40 0 0 1 88 0 z"/>
    <circle cx="600" cy="100" r="5"/>
  </g>
</svg>

<h1 class="heading" style="left:321px">MAIN</h1>
<h1 class="heading" style="left:868px">COURSE</h1>

<div class="doodle" style="left:236px;top:144px;width:170px;height:52px;border-radius:26px" role="img" aria-label="Line doodles of tomato, onion and pepper"></div>
<div class="doodle" style="left:758px;top:144px;width:222px;height:52px;border-radius:26px" role="img" aria-label="Line doodles of cheese wedge and mushrooms"></div>
<div class="doodle" style="left:570px;top:280px;width:50px;height:50px" role="img" aria-label="Lemon slice doodle"></div>
<div class="doodle" style="left:566px;top:420px;width:56px;height:70px" role="img" aria-label="Onion doodle"></div>
<div class="doodle" style="left:588px;top:545px;width:54px;height:56px" role="img" aria-label="Tomato doodle"></div>
<div class="doodle" style="left:536px;top:610px;width:70px;height:60px" role="img" aria-label="Eggplant doodle"></div>
<div class="doodle" style="left:558px;top:775px;width:82px;height:92px" role="img" aria-label="Hen doodle"></div>
<div class="doodle" style="left:1054px;top:600px;width:50px;height:110px" role="img" aria-label="Spatula doodle"></div>
<div class="doodle" style="left:1024px;top:770px;width:84px;height:76px" role="img" aria-label="Chili peppers doodle"></div>
<div class="doodle" style="left:574px;top:935px;width:48px;height:56px" role="img" aria-label="Pear doodle"></div>
<div class="doodle" style="left:584px;top:1050px;width:62px;height:64px" role="img" aria-label="Mushroom doodle"></div>
<div class="doodle" style="left:570px;top:1180px;width:68px;height:66px" role="img" aria-label="Carrot doodle"></div>
<div class="doodle" style="left:566px;top:1285px;width:84px;height:90px" role="img" aria-label="Beetroot doodle"></div>
<div class="doodle" style="left:1072px;top:1318px;width:54px;height:52px" role="img" aria-label="Cheese wedge doodle"></div>
<div class="doodle" style="left:530px;top:1392px;width:66px;height:96px" role="img" aria-label="Leaf doodle"></div>
<div class="doodle" style="left:612px;top:1510px;width:64px;height:64px" role="img" aria-label="Apple doodle"></div>
<div class="doodle" style="left:522px;top:1555px;width:72px;height:84px" role="img" aria-label="Garlic doodle"></div>
<div class="doodle" style="left:576px;top:1750px;width:46px;height:62px" role="img" aria-label="Olive doodle"></div>
<div class="doodle" style="left:538px;top:1850px;width:56px;height:86px" role="img" aria-label="Rosemary sprig doodle"></div>
<div class="doodle" style="left:198px;top:1932px;width:214px;height:60px;border-radius:30px" role="img" aria-label="Line doodles of mushroom, leaf and tomato"></div>
<div class="doodle" style="left:486px;top:2056px;width:228px;height:26px;border-radius:13px" role="img" aria-label="Rolling pin doodle"></div>

<div class="photo photo-grilled" role="img" aria-label="Grilled chicken breast with green beans and french fries on a white oval plate"></div>
<div class="photo photo-milanese" role="img" aria-label="Breaded chicken Milanese with creamy spaghetti and green beans"></div>
<div class="photo photo-shrimp" role="img" aria-label="Baked shrimp scampi dishes topped with herbed crumbs"></div>
<div class="photo photo-stroganoff" role="img" aria-label="Beef stroganoff in creamy sauce over egg noodles with salad leaves"></div>
<div class="photo photo-steak" role="img" aria-label="Grilled steak topped with green herb sauce on a dark skillet"></div>

<section class="dish" style="left:300px;top:574px">
  <h2 class="dish-name">GRILLED CHICKEN WITH<br>MUSHROOM SAUCE |</h2>
  <p class="dish-name-ar">دجاج مشوي مع صوص الفطر</p>
  <p class="dish-desc">Grilled chicken breasts served with creamy spinach sauce and a side of french fries and green beans<br>55</p>
  <p class="dish-desc-ar">فيليه صدور الدجاج المشوية مقدمة مع صوص كريمة السبانخ و البطاطس المقلية و الفاصوليا الخضراء<br>55</p>
</section>

<section class="dish" style="left:893px;top:574px">
  <h2 class="dish-name">CHICKEN MILANESE |</h2>
  <p class="dish-name-ar">دجاج ميلانيز</p>
  <p class="dish-desc" style="margin-top:18px">Fried breaded chicken breasts served with spaghetti with cream sauce and a side of green beans&nbsp;&nbsp;55</p>
  <p class="dish-desc-ar">فيليه صدور الدجاج المغطاة بالبقسماط، مقلية و مقدمة مع سباجيتي بالكريمة و الفاصوليا الخضراء&nbsp;&nbsp;55</p>
</section>

<section class="dish" style="left:302px;top:1303px">
  <h2 class="dish-name">SHRIMP SCAMPI BAKE |</h2>
  <p class="dish-name-ar">جمبري سكامبي بالفرن</p>
  <p class="dish-desc" style="margin-top:16px">Shrimps baked with mashed potatos, bechamel sauce, and mozzarella cheese. Served with spaghetti pasta and green beans&nbsp;&nbsp;55</p>
  <p class="dish-desc-ar">طاجن الجمبري و البطاطس المهروسة، مخبوز في الفرن مع البشاميل و الجبنة، و يقدم مع معكرونة السباجيتي و الفاصوليا الخضراء<br>55</p>
</section>

<section class="dish" style="left:893px;top:1303px">
  <h2 class="dish-name">BEEF STROGANOFF |</h2>
  <p class="dish-name-ar">لحم ستروغونوف</p>
  <p class="dish-desc" style="margin-top:34px">Thinly sliced beef cooked with creamy stroganoff sauce &amp; mushrooms, served with white rice&nbsp;&nbsp;55</p>
  <p class="dish-desc-ar">شرائح اللحم البقري الخفيفة مع صوص كريمة الستروغونوف و المشروم، مقدمة مع الأرز الأبيض&nbsp;&nbsp;55</p>
</section>

<section class="dish" style="left:300px;top:1655px">
  <h2 class="dish-name">STEAK WITH HERB SAUCE |</h2>
  <p class="dish-name-ar">ستيك مع صوص الأعشاب</p>
  <p class="dish-desc" style="margin-top:32px">Grilled filliet mignion topped with creamy green herbs sauce, served with a side of french fries and green beans&nbsp;&nbsp;65</p>
  <p class="dish-desc-ar">شرائح لحم الفيليه المشوية، مقدمة مع صوص الكريمة و الأعشاب و البطاطس المقلية و الفاصوليا الخضراء&nbsp;&nbsp;65</p>
</section>

</main>
</body>
</html>
```